Luxury Wine Label for New Startup Winery

We need a wine label for our new winery startup. We have worked with a local designer but do not feel the resulting label / logo have the elevation required to present our brand as a luxury wine. Our winery is called "Quailbrook Vineyards" and we are focused on extremely high quality hand crafted artisan and estate wines from the Pacific Northwest.
We would like to see designs that utilize a tree line, or other imagery that represents the "Quailbrook" part of our company name. Another interesting feature could be wood grain.
A logo will be required based on your design so please design with this in mind:
This logo should be consistent with the wine bottle label design, and should be representative of our high end exclusive wine while giving a sense of place (Oregon/ Pacific Northwest.)
I will supply an image of the design we received from our local designer, PLEASE NOTE: in general we do like wood grain and tree line concepts but feel the execution was poorly done.
ATTN: Logo design should be suitable for use on: Bottles (Red wine/rose/white wine), Bussiness cards, vehicle signage, business signage, etc
P.S.:
If you have a design that is not outside the box we are still interested in seeing it.
Label is for a burgundy style bottle with a label height of 3.5 - 4" and a width of 3.5-4"
any label <= 4"x4" and >=3.5"x3.5" will be acceptable:
HOWEVER Width should be greater than or equal to height due to the bottle format
Target Market(s)
Wine enthusiasts with adequate discretionary budgets to afford $100 bottles of wine.
Industry/Entity Type
Wine / Winery
Requirements
Must have
- A sense of luxury, a feel of exclusivity, and a theme consistent with our product and brand name
Nice to have
- Tree line, wood grain or other wood themes. Serif fonts
Should not have
- anything cheesy, off topic, hard to read script fonts or anything that makes the label hard to read from a few feet away or too busy

```html
<!DOCTYPE html>
<html lang="en">
<head>
<meta charset="utf-8">
<title>Quailbrook Vineyards – Syrah Label</title>
<link href="https://fonts.googleapis.com/css2?family=Cinzel:wght@500;600&family=Pinyon+Script&display=swap" rel="stylesheet">
<style>
  :root {
    --canvas-bg: #edf0f1;
    --label-black: #000000;
    --rule-olive: #706b55;
    --gold-deep: #d2bb5a;
    --gold-mid: #e2d59e;
    --gold-light: #f3eedd;
    --gold-end: #ddd19c;
    --wood-red: #743a22;
    --wood-mid: #5a2c1b;
    --wood-dark: #311a14;
    --tan: #d9ab7c;
    --tan-muted: #a86d48;
  }
  * { margin: 0; padding: 0; box-sizing: border-box; }
  html, body { width: 1200px; height: 1200px; overflow: hidden; background: var(--canvas-bg); }
  .canvas { position: relative; width: 1200px; height: 1200px; }

  .main-label {
    position: absolute; left: 299px; top: 319px; width: 602px; height: 401px;
    background: var(--label-black);
  }
  .rule { position: absolute; left: 17px; width: 566px; height: 5px; background: var(--rule-olive); }
  .rule--top { top: 33px; }
  .rule--bottom { top: 369px; }
  .treeline {
    position: absolute; left: 17px; top: 38px; width: 566px; height: 138px;
    background:
      linear-gradient(174deg, rgba(0,0,0,0) 0%, rgba(0,0,0,0) 22%, rgba(0,0,0,0.55) 45%, rgba(0,0,0,0.92) 66%, #000 80%),
      linear-gradient(to right, var(--gold-deep) 0%, var(--gold-mid) 35%, var(--gold-light) 62%, var(--gold-end) 100%);
  }
  .brand {
    position: absolute; left: 0; width: 100%; text-align: center;
    font-family: "Cinzel", serif; font-weight: 600; line-height: 1;
    background: linear-gradient(to right, var(--gold-deep) 10%, var(--gold-light) 50%, var(--gold-deep) 90%);
    -webkit-background-clip: text; background-clip: text; color: transparent;
  }
  .brand--name { top: 196px; font-size: 47px; letter-spacing: 7px; padding-left: 7px; }
  .brand--vineyards { top: 250px; font-size: 50px; letter-spacing: 6px; padding-left: 6px; }
  .brand--region { top: 314px; font-size: 31px; letter-spacing: 3px; padding-left: 3px; }

  .varietal-label {
    position: absolute; left: 300px; top: 739px; width: 599px; height: 142px;
    background: linear-gradient(to bottom,
      var(--wood-dark) 0%, var(--wood-red) 5%, var(--wood-red) 30%, var(--wood-mid) 40%,
      var(--wood-dark) 48%, var(--wood-red) 56%, var(--wood-red) 70%, var(--wood-mid) 80%,
      var(--wood-red) 90%, var(--wood-dark) 100%);
  }
  .grain { position: absolute; inset: 0; }
  .bar { position: absolute; height: 5px; background: var(--tan); }
  .bar--top { left: 17px; top: 11px; width: 565px; }
  .bar--left { left: 17px; top: 123px; width: 107px; }
  .bar--right { left: 476px; top: 123px; width: 106px; }
  .varietal {
    position: absolute; left: 0; top: 30px; width: 100%; text-align: center;
    font-family: "Pinyon Script", cursive; font-size: 72px; line-height: 1; color: var(--tan);
  }
  .vintage {
    position: absolute; left: 0; top: 115px; width: 100%; text-align: center;
    font-family: "Cinzel", serif; font-weight: 500; font-size: 22px; letter-spacing: 3px;
    color: var(--tan-muted); line-height: 1;
  }
  .vintage .sep { display: inline-block; margin: 0 6px; }
</style>
</head>
<body>
<div class="canvas">
  <section class="main-label">
    <div class="rule rule--top"></div>
    <div class="treeline" role="img" aria-label="Silhouette of an evergreen tree line against a golden sky"></div>
    <div class="brand brand--name">QUAILBROOK</div>
    <div class="brand brand--vineyards">VINEYARDS</div>
    <div class="brand brand--region">WILIAMETTE VALLEY</div>
    <div class="rule rule--bottom"></div>
  </section>

  <section class="varietal-label">
    <div class="grain" role="img" aria-label="Dark reddish-brown wood grain texture"></div>
    <div class="bar bar--top"></div>
    <div class="varietal">Syrah</div>
    <div class="bar bar--left"></div>
    <div class="vintage">ESTATE<span class="sep">|</span>2023<span class="sep">|</span>GROWN</div>
    <div class="bar bar--right"></div>
  </section>
</div>
</body>
</html>
```